Create a premium soap bar box bar design for an all-natural, men's skincare brand.

We are launching a men’s premium, natural soap bar and skincare business. To start, we will be launching cold-press, all-natural soap bars with a few additional products such as lotions. We plan to expand our line into additional skincare products such as face exfoliants, moisturizers and cleansers that target basic needs such as anti-aging, clarifying and hydrating.

Our target audience is men ages 25-50, with a secondary audience of male teens. Our target audience are mid to high income, professionals that live in more urban areas, but enjoy being active outdoors after work and on the weekends. Our target audience are hard workers, humble and want to enjoy all that life has to offer – whether that’s on top of a mountain or an ocean wave. They hike, bike, skateboard, surf or any other sport that gets them outside. They are husbands, brothers and fathers – there for their family and friends.

Our brand is sophisticated, adventurous and has a sense of humor. Many of our competitors either focus on the rugged outdoors or are more pretentious. We are in-between. We are free spirited and love the fresh air. Our products are trustworthy with no toxic chemicals or harsh ingredients. We are all-natural and provide high-quality, premium products that our audience expects and deserves.

Target Market(s)

Men, ages 25-54 who are high-earning professionals, yet enjoy getting outdoors and being active on the weekends - hiking, biking, surfing, skateboarding and more.

Industry/Entity Type

Men's skincare

Font styles to use
Sans Serif

Requirements
Must have
• See attachments
Nice to have
• We would prefer to a have a premium, slightly more modern looking design that will appeal to our target audience and slightly higher price point.
Should not have
• Please do not include an icon for the fragrance, i.e. cinnamon sticks. However, we do need some differentiation for the fragrance, i.e. color, etc. as it will be on the shelf with other fragrances.

```html
<!DOCTYPE html>
<html lang="en">
<head>
<meta charset="utf-8">
<title>Hale Ridge – Cinnamon Bark Soap Box</title>
<link rel="stylesheet" href="https://fonts.googleapis.com/css2?family=Jost:wght@500;700;800&display=swap">
<style>
  :root {
    --page: #ffffff;
    --bark-red: #6b1a1f;
    --bark-deep: #45100f;
    --kraft: #caa273;
    --navy: #1e3953;
    --coral: #e2585b;
  }
  html, body {
    margin: 0;
    width: 1200px;
    height: 960px;
    overflow: hidden;
    background: var(--page);
    font-family: "Jost", sans-serif;
  }
  .box-dieline {
    position: absolute;
    left: 311px;
    top: 70px;
    width: 577px;
    height: 820px;
    display: block;
  }
  .label-text {
    font-family: "Jost", sans-serif;
    paint-order: stroke fill;
    stroke-linejoin: round;
  }
</style>
</head>
<body>
<svg class="box-dieline" viewBox="0 0 577 820" xmlns="http://www.w3.org/2000/svg">
  <defs>
    <linearGradient id="barkTone" x1="0" y1="0" x2="0" y2="1">
      <stop offset="0" stop-color="#5a1519"/>
      <stop offset="0.5" stop-color="#701b20"/>
      <stop offset="1" stop-color="#5e161a"/>
    </linearGradient>
  </defs>

  <!-- side panel -->
  <g class="side-panel">
    <rect class="side-bark-fill" x="0" y="0" width="154" height="820" fill="url(#barkTone)"
          role="img" aria-label="Dark red cinnamon bark wood-grain texture"/>
    <g class="side-directions" fill="var(--navy)">
      <text class="label-text" transform="translate(58 680) rotate(-90)" font-size="38" font-weight="800"
            stroke="var(--kraft)" stroke-width="7" textLength="580" lengthAdjust="spacingAndGlyphs">DIRECTIONS: LATHER,</text>
      <text class="label-text" transform="translate(98 680) rotate(-90)" font-size="38" font-weight="800"
            stroke="var(--kraft)" stroke-width="7" textLength="540" lengthAdjust="spacingAndGlyphs">RINSE AND REPEAT.</text>
      <text class="label-text" transform="translate(121 680) rotate(-90)" font-size="17" font-weight="700"
            stroke="var(--kraft)" stroke-width="4" textLength="600" lengthAdjust="spacingAndGlyphs">CHECK OUT ALL OUR PRODUCTS AT HALERIDGE.COM</text>
    </g>
    <g class="side-brand">
      <circle cx="22" cy="746" r="9" fill="var(--kraft)"/>
      <text class="label-text" x="36" y="753" font-size="19" font-weight="500" fill="var(--kraft)">HALE RIDGE</text>
    </g>
  </g>

  <!-- front panel -->
  <g class="front-panel" transform="translate(154 0)">
    <rect class="front-bark-fill" x="0" y="0" width="423" height="820" fill="url(#barkTone)"
          role="img" aria-label="Dark red cinnamon bark wood-grain texture"/>
    <g class="product-name" fill="var(--navy)" stroke="var(--kraft)">
      <text class="label-text" x="211" y="325" text-anchor="middle" font-size="60" font-weight="700"
            stroke-width="14" textLength="300" lengthAdjust="spacingAndGlyphs">CINNAMON</text>
      <text class="label-text" x="211" y="437" text-anchor="middle" font-size="132" font-weight="800"
            stroke-width="16" textLength="300" lengthAdjust="spacingAndGlyphs">BARK</text>
    </g>
    <g class="product-type">
      <circle cx="79" cy="487" r="8" fill="none" stroke="var(--coral)" stroke-width="3"/>
      <text class="label-text" x="96" y="496" font-size="26" font-weight="700" fill="var(--coral)"
            stroke="var(--kraft)" stroke-width="7" textLength="254" lengthAdjust="spacingAndGlyphs">MEN’S NATURAL SOAP</text>
    </g>
    <g class="brand-band">
      <rect x="0" y="680" width="423" height="114" fill="var(--kraft)"/>
      <circle cx="96" cy="737" r="30" fill="none" stroke="var(--navy)" stroke-width="3"/>
      <text class="label-text" x="140" y="752" font-size="40" font-weight="500" fill="var(--navy)"
            textLength="220" lengthAdjust="spacingAndGlyphs">HALE RIDGE</text>
    </g>
  </g>
</svg>
</body>
</html>
```